Simple and Clean business card design

We would like the design to be simple clean and to incorporate our colors.

We are open to your design and talent, we have the dots in our logo as we think of it as data points and we connect data points for people.

We are open to see the great creative and clean design you bring to the table

Contact Information for Business Card

please include: name, position, email, phone and website

Font styles to use
Sans Serif

Requirements
Must have
• my colors incorporated, simplicity
Nice to have
• lots of white space, simplicity
Should not have
• complexicity/ complex art

```html
<!DOCTYPE html>
<html lang="en">
<head>
<meta charset="utf-8">
<title>Nodal business card</title>
<link rel="stylesheet" href="https://fonts.googleapis.com/css2?family=Jost:wght@400;500;700&display=swap">
<style>
  :root {
    --ink: #161616;
    --text: #3a3a3a;
    --paper: #ffffff;
    --backdrop: #e9e9e9;
    --blue: #5f86c5;
    --green: #33a853;
  }
  * { margin: 0; padding: 0; box-sizing: border-box; }
  html, body { width: 1021px; height: 1200px; overflow: hidden; }
  body {
    position: relative;
    background: var(--backdrop);
    font-family: "Jost", sans-serif;
    color: var(--text);
  }
  .card {
    position: absolute;
    width: 753px;
    height: 429px;
    background: var(--paper);
  }
  .card--front { left: 134px; top: 119px; }
  .card--back { left: 131px; top: 651px; }

  .wordmark {
    display: flex;
    align-items: center;
    gap: 14px;
    font-weight: 500;
    color: var(--ink);
    line-height: 1;
  }
  .wordmark__dot {
    border-radius: 50%;
    background: var(--blue);
    flex: none;
  }
  .card--front .wordmark {
    position: absolute;
    left: 0; right: 0; top: 150px;
    justify-content: center;
    font-size: 140px;
    letter-spacing: 2px;
  }
  .card--front .wordmark__dot { width: 30px; height: 30px; margin-top: 60px; }

  .card--back .wordmark {
    position: absolute;
    left: 39px; top: 66px;
    font-size: 74px;
    gap: 8px;
  }
  .card--back .wordmark__dot { width: 16px; height: 16px; margin-top: 34px; }

  .company {
    position: absolute;
    right: 42px; top: 252px;
    font-size: 30px;
    font-weight: 700;
    color: var(--green);
    line-height: 1;
  }
  .role {
    position: absolute;
    right: 42px; top: 285px;
    font-size: 19px;
    line-height: 1;
  }
  .accent-bar {
    position: absolute;
    right: 0; top: 260px;
    width: 18px; height: 44px;
    background: var(--blue);
  }
  .divider {
    position: absolute;
    left: 39px; top: 298px;
    width: 542px; height: 1px;
    background: var(--blue);
  }
  .contacts {
    position: absolute;
    left: 39px; top: 312px;
    list-style: none;
    font-size: 19px;
    line-height: 27px;
  }
  .contacts li { display: flex; align-items: center; gap: 8px; }
  .contacts svg { width: 15px; height: 15px; flex: none; }
</style>
</head>
<body>
  <section class="card card--front">
    <div class="wordmark"><span class="wordmark__dot"></span>Nodal</div>
  </section>

  <section class="card card--back">
    <div class="wordmark"><span class="wordmark__dot"></span>Nodal</div>

    <p class="company">NODAL.ONE</p>
    <p class="role">Founder/ CEO</p>
    <span class="accent-bar"></span>
    <span class="divider"></span>

    <ul class="contacts">
      <li>
        <svg viewBox="0 0 16 16" aria-hidden="true"><path fill="var(--green)" d="M3.5 1.5l2.5 0 1 3.5-1.6 1.1a8 8 0 0 0 4.5 4.5L11 9l3.5 1v2.5c0 1-1 2-2 2C6.7 14.5 1.5 9.3 1.5 3.5c0-1 1-2 2-2z"/></svg>
        555-214-0387
      </li>
      <li>
        <svg viewBox="0 0 16 16" aria-hidden="true"><rect x="1" y="3" width="14" height="10" fill="var(--green)"/><path d="M1.5 3.5L8 9l6.5-5.5M1.5 12.5l4.5-4.5M14.5 12.5L10 8" stroke="#fff" stroke-width="1.2" fill="none"/></svg>
        dana.reyes@nodal.one
      </li>
      <li>
        <svg viewBox="0 0 16 16" aria-hidden="true"><circle cx="8" cy="8" r="7" fill="var(--green)"/><path d="M4 4.5c1.5 0 2.5 1 2 2.5s1 2 1 3.5-1 2-1.5 2.5M10 2.5c-.5 1.5.5 2.5 2 2.5s1.5 2 .5 3.5" stroke="#fff" stroke-width="1.3" fill="none"/></svg>
        www.Nodal.one
      </li>
    </ul>
  </section>
</body>
</html>
```